Residential Remodeling Contractor needs updated business card

I need a new design for my business card.
Name of the company is Ridgefell Construction. I need a card that commands presence, strength, integrity. I have been in business for 28 years. I am a Residential Remodeling Contractor that covers all aspects of a residential remodel and build.

```html
<!DOCTYPE html>
<html lang="en">
<head>
<meta charset="UTF-8">
<title>Ridgefell Construction – Business Card</title>
<link href="https://fonts.googleapis.com/css2?family=Montserrat:wght@400;600;700&display=swap" rel="stylesheet">
<style>
  :root {
    --navy: #213b7d;
    --white: #ffffff;
    --soft-white: rgba(255,255,255,0.85);
    --divider: rgba(255,255,255,0.35);
    --backdrop: #e6e6e9;
  }
  * { margin: 0; padding: 0; box-sizing: border-box; }
  html, body {
    width: 1200px; height: 786px; overflow: hidden;
    background: var(--backdrop);
    font-family: "Montserrat", sans-serif;
  }
  .canvas {
    position: relative; width: 1200px; height: 786px;
    display: flex; align-items: center; justify-content: center; gap: 60px;
  }
  .card {
    position: relative; width: 520px; height: 298px;
    background: var(--navy); color: var(--white);
    overflow: hidden;
    box-shadow: 0 10px 28px rgba(0,0,0,0.22);
  }
  .card-band { position: absolute; left: 0; bottom: 0; width: 520px; height: 80px; }

  .wordmark { display: flex; align-items: center; gap: 10px; font-weight: 600; letter-spacing: 0.06em; text-transform: uppercase; }
  .wordmark-square { width: 14px; height: 14px; background: var(--white); flex: none; }
  .wordmark-name { line-height: 1.2; }

  .contact-side .wordmark { position: absolute; left: 34px; top: 112px; font-size: 16px; }
  .divider { position: absolute; left: 220px; top: 48px; width: 1px; height: 150px; background: var(--divider); }

  .details { position: absolute; left: 242px; top: 44px; }
  .person-name { font-size: 19px; font-weight: 700; }
  .person-role { font-size: 10px; font-weight: 400; color: var(--soft-white); margin-top: 2px; }
  .address { font-size: 11px; line-height: 1.3; margin-top: 16px; }
  .contact-list { list-style: none; margin-top: 12px; }
  .contact-list li { display: flex; align-items: center; gap: 10px; font-size: 11px; margin-bottom: 7px; }
  .contact-list svg { width: 13px; height: 13px; flex: none; }

  .logo-side { display: flex; align-items: center; justify-content: center; }
  .logo-side .wordmark { font-size: 26px; gap: 14px; }
  .logo-side .wordmark-square { width: 20px; height: 20px; }
</style>
</head>
<body>
<main class="canvas">
  <section class="card contact-side">
    <svg class="card-band" viewBox="0 0 520 80" aria-hidden="true">
      <polygon points="0,70 310,70 316,50 520,50 520,80 0,80" fill="#ffffff"/>
      <polygon points="300,80 316,50 326,50 310,80" fill="#213b7d"/>
    </svg>
    <div class="wordmark">
      <span class="wordmark-square"></span>
      <span class="wordmark-name">Ridgefell<br>Construction</span>
    </div>
    <div class="divider"></div>
    <div class="details">
      <p class="person-name">Daniel Hartwell</p>
      <p class="person-role">Owner</p>
      <p class="address">248 Cedar Hollow Road<br>Brookvale, MS 39052</p>
      <ul class="contact-list">
        <li>
          <svg viewBox="0 0 16 16"><path d="M3 2h3l1.5 3.5-2 1.2a9 9 0 0 0 3.8 3.8l1.2-2L14 10v3a1 1 0 0 1-1 1A12 12 0 0 1 2 3a1 1 0 0 1 1-1z" fill="#fff"/></svg>
          <span>601.555.0147</span>
        </li>
        <li>
          <svg viewBox="0 0 16 16"><rect x="1" y="3" width="14" height="10" fill="#fff"/><path d="M1 3l7 6 7-6" fill="none" stroke="#213b7d" stroke-width="1.4"/></svg>
          <span>info@ridgefellconstruction.com</span>
        </li>
        <li>
          <svg viewBox="0 0 16 16"><circle cx="8" cy="8" r="6.5" fill="none" stroke="#fff" stroke-width="1.4"/><ellipse cx="8" cy="8" rx="2.8" ry="6.5" fill="none" stroke="#fff" stroke-width="1.2"/><line x1="1.5" y1="8" x2="14.5" y2="8" stroke="#fff" stroke-width="1.2"/></svg>
          <span>www.ridgefellconstruction.com</span>
        </li>
      </ul>
    </div>
  </section>

  <section class="card logo-side">
    <div class="wordmark">
      <span class="wordmark-square"></span>
      <span class="wordmark-name">Ridgefell<br>Construction</span>
    </div>
  </section>
</main>
</body>
</html>
```